Webdesign für Sexualpädagogik
Zielgruppe
- Sexualpädagogik, Beratung und Sexualtherapie
- Vorträge und Seminare für Unternehmen / Institutionen Vorträge Sexualität in der Pflege / im Alter / Grenzen wahrnehmen
- Wechseljahreberatung, Beratung in der Lebensmitte
- ZIelgruppe: Menschen, die sich weiternetwickeln möchten, die Problme mit ihrer Sexualität haben, Paare, Jugendliche
letztes Interview in der Zeitung: https://www.talpost-beispiel.ch/nachrichtenblatt/zeitung/frontal-interview/sexualitaet-hoert-nicht-beim-eintritt-ins-spital-auf/
Aufgabenstellung
- bestehende Internetseite siehe unten: Schrift ist Especial Key von Tauwerk Mitte
- auf dem Briefpapier bisher noch der Fachbuchhandel und Onlinhandel, aber beides nicht mehr
- Bilder zum Thema bereist vorhanden
- für Werbeflyer habe ich die Therapie in dunkelblau gehalten udn in der sexualpädagogik in hellblau
der kramkiste wird aus der website entfernet

```html
<!DOCTYPE html>
<html lang="de">
<head>
<meta charset="utf-8">
<title>Tauwerk Mitte – Mira Halden</title>
<link rel="stylesheet" href="https://fonts.googleapis.com/css2?family=Raleway:wght@300;400;500;700&family=Roboto:wght@300;400;500;700&display=swap">
<style>
:root{
  --blue:#1a96dc;
  --text:#3e3e3e;
  --muted:#6a6a6a;
  --line:#6f6f6f;
  --hero-a:#cfd8dc;
  --hero-b:#e8e4df;
  --band:#8b8b8b;
  --card:rgba(243,243,243,.9);
  --foot-a:#a9b8c6;
  --foot-b:#e9d9d4;
}
*{margin:0;padding:0;box-sizing:border-box}
html,body{width:1200px;height:2288px;overflow:hidden;background:#fff}
body{position:relative;font-family:'Raleway',sans-serif;color:var(--text)}
.abs{position:absolute}
.hero{left:0;top:0;width:1200px;height:754px;background:linear-gradient(90deg,var(--hero-a) 0%,#dfe3e3 45%,var(--hero-b) 100%)}
.hero-photo{left:360px;top:80px;width:840px;height:674px;background:radial-gradient(ellipse at 60% 45%,#d9b3a0 0%,#c79a86 25%,#b8c4d8 60%,rgba(220,220,225,0) 80%)}
.nav{top:27px;font-size:12px;color:#555;letter-spacing:.2px}
.brand-mark{left:210px;top:335px;font-size:42px;font-weight:400;color:var(--blue);display:flex;align-items:center;gap:14px}
.brand-mark i{display:block;width:22px;height:22px;border-radius:50%;background:var(--blue)}
.hero-name{left:134px;top:462px;font-size:48px;font-weight:700;color:var(--blue);line-height:1}
.hero-role{left:134px;top:512px;font-size:40px;font-weight:400;color:var(--blue);line-height:1}
.btn{position:absolute;border:1px solid var(--line);border-radius:3px;display:flex;align-items:center;justify-content:center;font-family:'Roboto',sans-serif;font-weight:300;color:#555;background:transparent}
.quote{left:0;top:822px;width:1200px;text-align:center;font-family:'Roboto',sans-serif;font-size:29px;line-height:33px;color:#444}
.band{left:0;top:1041px;width:1200px;height:633px;background:linear-gradient(120deg,#7a7a7a,#a9a9a9 45%,#8c8c8c)}
.card{position:absolute;top:1118px;width:328px;height:479px;background:var(--card);text-align:center}
.card svg{position:absolute;left:50%;transform:translateX(-50%);top:36px}
.card h2{position:absolute;top:126px;width:100%;font-size:22px;font-weight:700;color:var(--blue);letter-spacing:.2px}
.card p{position:absolute;top:192px;left:30px;right:30px;font-size:20px;font-weight:300;line-height:24px;color:#333}
.card .btn{border-color:var(--blue);color:var(--blue);font-size:15px;width:95px;height:37px;top:407px}
.info h3{font-family:'Roboto',sans-serif;font-size:17px;font-weight:500;color:#444;position:absolute}
.info p{position:absolute;font-size:14px;font-weight:300;line-height:19px;color:#555}
.field{position:absolute;border:1px solid var(--line);border-radius:3px;font-size:11px;color:#555;padding-left:8px;display:flex;align-items:center;font-family:'Roboto',sans-serif}
.footer{left:0;top:1922px;width:1200px;height:332px;background:linear-gradient(90deg,var(--foot-a) 0%,#c6c9d2 45%,var(--foot-b) 100%)}
.foot-mark{left:86px;top:2140px;font-size:26px;color:#555;display:flex;align-items:center;gap:10px}
.foot-mark i{display:block;width:14px;height:14px;border-radius:50%;background:#555}
.footer-col h4{position:absolute;top:1994px;font-family:'Roboto',sans-serif;font-size:17px;font-weight:500;color:#3a3a3a}
.footer-col p{position:absolute;font-size:14px;font-weight:300;line-height:19px;color:#555}
.legal{top:2266px;font-family:'Roboto',sans-serif;font-size:15px;color:var(--blue)}
</style>
</head>
<body>

<section class="abs hero" role="img" aria-label="Hintergrundfoto: Büroraum, unscharf"></section>
<div class="abs hero-photo" role="img" aria-label="Porträtfoto der Sexualtherapeutin"></div>

<nav>
  <span class="abs nav" style="left:577px">HOME</span>
  <span class="abs nav" style="left:653px">ÜBER MICH</span>
  <span class="abs nav" style="left:762px">WAS WIR TUN</span>
  <span class="abs nav" style="left:876px">SEMINAR</span>
  <span class="abs nav" style="left:966px">NEWS</span>
  <span class="abs nav" style="left:1043px">BLOG</span>
  <span class="abs nav" style="left:1110px">KONTAKT</span>
</nav>

<div class="abs brand-mark"><i></i>Tauwerk Mitte</div>
<h1 class="abs hero-name">Mira Halden</h1>
<div class="abs hero-role">sexualtherapeutin</div>
<a class="btn" style="left:216px;top:588px;width:167px;height:39px;font-size:15px">MEHR ERFAHREN</a>

<blockquote class="abs quote">„Wenn wir uns selbst nicht lieben,<br>können wir auch keinen anderen Menschen lieben.”</blockquote>
<a class="btn" style="left:419px;top:932px;width:162px;height:37px;font-size:15px">ÜBER MICH</a>
<a class="btn" style="left:618px;top:932px;width:162px;height:37px;font-size:15px">TERMIN</a>

<section class="abs band" role="img" aria-label="Hintergrundfoto: Paar umarmt sich, in Grautönen"></section>

<article class="card" style="left:89px">
  <svg width="60" height="60" viewBox="0 0 60 60" fill="none" stroke="#1a96dc" stroke-width="5">
    <circle cx="18" cy="38" r="11"/><path d="M26 30 L38 8 M30 8h8v8"/>
    <circle cx="42" cy="30" r="11"/><path d="M42 41v17 M35 51h14"/>
  </svg>
  <h2>SEXUALBERATUNG</h2>
  <p>Lorem ipsum dolor sit amet, consectetur adipis-cing elit, sed do eiusmod tempor incididunt ut labore et dolore magna aliqua.</p>
  <a class="btn" style="left:105px">MEHR</a>
</article>

<article class="card" style="left:435px">
  <svg width="60" height="60" viewBox="0 0 60 60" fill="none" stroke="#1a96dc" stroke-width="3">
    <path d="M22 56v-10c-8-4-12-12-12-20 0-12 9-21 21-21s20 9 20 20c0 4-1 6-3 9l4 7h-5v6c0 3-3 5-6 5h-5v4"/>
    <path d="M31 34l-8-8c-3-3 0-8 4-7 2 0 3 2 4 3 1-1 2-3 4-3 4-1 7 4 4 7z"/>
  </svg>
  <h2>SEXUALPÄDAGOGIK</h2>
  <p>Gravida neque convallis a cras semper auctor neque vitae. Morbi non arcu risus quis varius quam quisque id diam. Senectus et netus et malesuada fames ac.</p>
  <a class="btn" style="left:116px;top:413px">MEHR</a>
</article>

<article class="card" style="left:782px">
  <svg width="60" height="60" viewBox="0 0 60 60" fill="#1a96dc">
    <rect x="14" y="4" width="32" height="5"/><rect x="14" y="51" width="32" height="5"/>
    <path d="M17 9h26c0 10-9 14-9 21s9 11 9 21H17c0-10 9-14 9-21s-9-11-9-21z"/>
  </svg>
  <h2>WECHSELJAHRBERATUNG</h2>
  <p>Gravida rutrum quisque non tellus orci ac. Nec ul-lamcorper sit amet risus nullam eget. Mattis moles-tie a iaculis at erat pellen-tesque adipiscing.</p>
  <a class="btn" style="left:122px;top:413px">MEHR</a>
</article>

<section class="info">
  <h3 style="left:147px;top:1738px">Nächste Seminare</h3>
  <p style="left:147px;top:1775px;width:230px">Lorem ipsum dolor sit amet, con-sectetur adipiscing elit, sed do eiusmod: 11. AUG. 2018.</p>
  <h3 style="left:484px;top:1738px">Aus den Medien</h3>
  <p style="left:480px;top:1775px;width:245px">Lorem ipsum dolor sit amet, con-sectetur adipiscing elit, sed do eius-mod tempor incididunt ut labore et dolore magna aliqua.</p>
  <h3 style="left:826px;top:1736px">Empfehlen Sie uns weiter</h3>
  <div class="field" style="left:826px;top:1777px;width:259px;height:28px">E-MAIL ADRESSE</div>
  <a class="btn" style="left:826px;top:1819px;width:74px;height:28px;font-size:11px">SENDEN</a>
</section>

<footer>
  <div class="abs footer" role="img" aria-label="Hintergrundfoto: Hände halten einen herzförmigen Stein"></div>
  <div class="abs foot-mark"><i></i>Tauwerk Mitte</div>
  <div class="footer-col">
    <h4 style="left:326px">TAUWERK MITTE</h4>
    <p style="left:326px;top:2032px">Mira Halden<br>Sexualtherapeutin</p>
    <p style="left:326px;top:2087px">Lindenweg 12<br>3000 Talstadt</p>
    <p style="left:326px;top:2145px">Telefon: +41 (0)00 555 01 23<br>E-mail: &nbsp;&nbsp;&nbsp;info@tauwerk-mitte.example</p>
    <h4 style="left:619px">MENU</h4>
    <p style="left:619px;top:2032px;line-height:24.3px">Home<br>Über mich<br>Was wir tun<br>Seminare<br>News<br>Blog<br>Kontakt</p>
    <h4 style="left:826px">NEWSLETTER</h4>
  </div>
  <div class="field" style="left:826px;top:2035px;width:259px;height:28px">NAME</div>
  <div class="field" style="left:826px;top:2074px;width:259px;height:28px">E-MAIL ADRESSE</div>
  <a class="btn" style="left:826px;top:2130px;width:74px;height:28px;font-size:11px">SENDEN</a>
  <span class="abs legal" style="left:84px">DATENSCHUTZ</span>
  <span class="abs legal" style="left:240px">IMPRESSUM</span>
  <span class="abs legal" style="left:932px">MIRA HALDEN | 2018</span>
</footer>

</body>
</html>
```